I need a website designed. I am a mortgage loan officer and would like to have a website for me and my team where i can post resources, videos and blog information for my clients. A website like themorvaskteam.com .

The theme is - The Pelkins Team - Home Loan Group powered by Brightwell Home Loans -

Target Market(s)

B2B (Real Estate Agents)and B2C (Home buyers and refinancing)

Industry/Entity Type

Mortgage Lender

Coding

Coded - Design and coding required

Number of Pages Required

5+ page

Font styles to use
Serif
Sans Serif

Colors

Designer to choose colors to be used in the design.

Requirements
Must have
• Disclaimers: Licensed by the Bureau of Lending Affairs under the Pacific Credit Providers Act. Loans made or arranged pursuant to a Pacific Credit Providers Act License. Equal Housing Lender Brightwell Cannot Accept mortgage applications for properties located in New York via this site
• Mobile Friendly
Nice to have
• Main Links: Home, About Us(see team flyer), Mortgage 101, Contact Us (formzig form)

```html
<!DOCTYPE html>
<html lang="en">
<head>
<meta charset="utf-8">
<title>The Pelkins Team – Home Loan Group</title>
<link rel="stylesheet" href="https://fonts.googleapis.com/css2?family=Bebas+Neue&family=Raleway:wght@400;500;600;700&display=swap">
<style>
:root{
  --blue:#1268b3;
  --blue-dark:#0d4f8c;
  --navy:#15263a;
  --ink:#222;
  --text:#555;
  --light:#f5f3ef;
  --grey-band:#7a7a7a;
  --footer:#333333;
  --footer-text:#cfcfcf;
  --white:#fff;
}
*{box-sizing:border-box;margin:0;padding:0}
html,body{width:1200px;height:3297px;overflow:hidden}
body{position:relative;background:var(--white);font-family:"Raleway",Arial,sans-serif;color:var(--text)}
.heading{font-family:"Bebas Neue","Oswald",sans-serif;font-weight:400;letter-spacing:2px;color:var(--ink)}
.abs{position:absolute}
a{color:inherit;text-decoration:none}

/* Header */
.site-header{left:0;top:0;width:1200px;height:105px;background:var(--light)}
.brand{left:88px;top:22px;display:flex;align-items:center;gap:12px}
.brand-mark{width:34px;height:34px;background:var(--blue)}
.brand-name{font-family:"Raleway",sans-serif;font-weight:700;font-size:19px;color:var(--blue-dark);line-height:1.1}
.main-nav{right:88px;top:42px;display:flex;gap:52px;font-family:"Raleway",sans-serif;font-size:13px;font-weight:600;color:#333;letter-spacing:1px}

/* Hero */
.hero{left:0;top:105px;width:1200px;height:506px;background:linear-gradient(180deg,#8a6a2e 0%,#c59540 35%,#6d5a2a 70%,#3b3a22 100%)}
.hero-title{left:0;width:1200px;top:156px;text-align:center;font-size:60px;color:var(--white);letter-spacing:4px}
.hero-text{left:290px;width:620px;top:228px;text-align:center;color:var(--white);font-size:15px;line-height:26px}
.btn{display:inline-block;background:var(--blue);color:var(--white);font-family:"Bebas Neue",sans-serif;letter-spacing:1.5px;text-align:center}
.hero-btn{left:519px;top:293px;width:158px;height:40px;line-height:40px;font-size:21px}
.hero-dots{left:1151px;top:235px;display:flex;flex-direction:column;gap:7px}
.hero-dots span{width:11px;height:11px;border:1.5px solid var(--white);border-radius:50%}
.hero-dots span.active{background:var(--blue);border-color:var(--blue)}

/* About */
.about-media{left:88px;top:673px;width:462px;height:345px;background:linear-gradient(135deg,#2aa7d6,#1587c4)}
.about-video{left:240px;top:919px;width:327px;height:189px;background:linear-gradient(135deg,#4a4a4a,#1e1e1e)}
.play{left:376px;top:987px}
.about-eyebrow{left:607px;top:704px;font-size:24px}
.about-title{left:607px;top:734px;font-size:42px;letter-spacing:3px}
.about-text{left:607px;width:500px;font-size:12px;line-height:20px;color:#666}
.about-btn{left:609px;top:1042px;width:138px;height:42px;line-height:42px;font-size:19px;box-shadow:3px 3px 0 var(--blue-dark)}

/* Resources */
.resources{left:0;top:1171px;width:1200px;height:412px;background:linear-gradient(90deg,#1b2c42,#13233a 50%,#1b2c42)}
.resources-title{left:0;width:1200px;top:1235px;text-align:center;font-size:40px;color:var(--white)}
.resource-card{top:1297px;width:332px;height:213px;background:var(--white);text-align:center;padding:22px 20px 0}
.resource-card h3{font-size:21px;line-height:24px;letter-spacing:1.5px}
.resource-card p{font-size:12.5px;line-height:24px;color:#444;margin-top:8px}
.resource-card .more{display:block;font-size:12.5px;color:#444;margin-top:20px}

/* Team */
.section-title{left:0;width:1200px;text-align:center;font-size:40px;color:var(--blue)}
.team-card{top:1723px;width:246px;height:343px;border:1px solid #ddd;text-align:center}
.team-photo{width:246px;height:207px;margin:-1px 0 0 -1px}
.team-card h3{font-size:23px;margin-top:8px;letter-spacing:1.5px}
.team-card .role{font-size:12.5px;font-weight:600;color:#333}
.team-card p{font-size:11.5px;line-height:19px;color:#555;padding:10px 14px 0;height:58px;overflow:hidden}

/* Blog */
.blog-post{top:2276px;width:321px}
.blog-post h3{font-size:21px;letter-spacing:1px}
.blog-image{width:321px;height:200px;margin-top:8px;border:1px solid #ccc}
.blog-post p{font-size:12px;line-height:19px;color:#666;margin-top:22px}
.blog-post .more{display:block;font-size:12px;color:#444;margin-top:26px}

/* Newsletter */
.newsletter{left:0;top:2754px;width:1200px;height:132px;background:var(--grey-band)}
.newsletter-title{left:222px;top:2800px;font-size:35px;color:var(--white);letter-spacing:3px}
.newsletter-input{left:550px;top:2798px;width:285px;height:44px;border:1.5px solid #ddd;color:#ddd;font-size:12px;padding:14px 18px}
.newsletter-btn{left:848px;top:2798px;width:128px;height:44px;line-height:44px;font-size:21px}

/* Footer */
.site-footer{left:0;top:2886px;width:1200px;height:411px;background:var(--footer);color:var(--footer-text)}
.footer-brand{left:88px;top:2956px;width:255px;text-align:center}
.footer-brand .brand-mark{margin:0 auto 10px;width:48px;height:48px}
.footer-brand .brand-name{font-size:24px;color:#3b85c4}
.footer-divider{width:1px;background:#555}
.footer-heading{font-size:17px;color:#e5e5e5}
.contact-list{left:470px;top:2970px;list-style:none;font-size:14px;line-height:20px}
.contact-list li{display:flex;gap:22px;margin-bottom:18px}
.contact-list svg{flex:none;margin-top:3px}
.links{left:1007px;top:2966px;list-style:none;font-size:12.5px;line-height:26px}
.legal{left:88px;width:1024px;top:3166px;font-size:12px;line-height:22px;color:#aaa;border-top:1px solid #555;padding-top:8px}
.copyright{left:88px;top:3258px;font-size:12px;color:#aaa}
.social{left:980px;top:3256px;display:flex;gap:18px}
.social span{width:14px;height:14px;border-radius:50%;background:#cfcfcf}
</style>
</head>
<body>

<header class="abs site-header">
  <div class="abs brand"><span class="brand-mark"></span><span class="brand-name">The Pelkins Team<br>Home Loan Group</span></div>
  <nav class="abs main-nav"><a href="#">HOME</a><a href="#">ABOUT US</a><a href="#">MORTGAGE 101</a><a href="#">CONTACT US</a></nav>
</header>

<section class="abs hero" role="img" aria-label="Photo of two hands exchanging a small wooden house and a money bag in warm sunset light"></section>
<h1 class="abs heading hero-title">PELKINS TEAM</h1>
<p class="abs hero-text">Lorem Ipsum is simply dummy text of the printing and typesetting industry. Lorem Ipsum has been the industry's standard dummy text ever since the 1500s.</p>
<a class="abs btn hero-btn" href="#">CALL US TODAY</a>
<div class="abs hero-dots"><span></span><span></span><span class="active"></span><span></span><span></span></div>

<div class="abs about-media" role="img" aria-label="Photo of the word LOANS shaped in clay with a small house on a blue background"></div>
<div class="abs about-video" role="img" aria-label="Video thumbnail showing loan paperwork"></div>
<svg class="abs play" width="54" height="54" viewBox="0 0 54 54"><circle cx="27" cy="27" r="24" fill="none" stroke="#1e8fe0" stroke-width="4"/><path d="M21 16 L38 27 L21 38 Z" fill="#1e8fe0"/></svg>
<h2 class="abs heading about-eyebrow">ABOUT US</h2>
<h2 class="abs heading about-title">PELKINS TEAM</h2>
<p class="abs about-text" style="top:800px">Contrary to popular belief, Lorem Ipsum is not simply random text. It has roots in a piece of classical Latin literature from 45 BC, making it over 2000 years old. Rowan Haldane, a Latin professor at Ashgrove College in Vermont, looked up one of the more obscure Latin words, consectetur, from a Lorem Ipsum passage, and going through the cites of the word in classical literature, discovered the undoubtable source.</p>
<p class="abs about-text" style="top:924px">Lorem Ipsum comes from sections 1.10.32 and 1.10.33 of "de Finibus Bonorum et Malorum" (The Extremes of Good and Evil) by Marcus Tullan, written in 45 BC. This book is a treatise on the theory of ethics, very popular during the Renaissance. The first line of Lorem Ipsum, "Lorem ipsum dolor sit amet..", comes from a line in section 1.10.32.</p>
<a class="abs btn about-btn" href="#">READ MORE &gt;</a>

<section class="abs resources"></section>
<h2 class="abs heading resources-title">RESOURCES</h2>
<article class="abs resource-card" style="left:88px"><h3 class="heading">SECTION 1.10.33 OF "DE FINIBUS BONORUM ET MALORUM</h3><p>Lorem Ipsum is simply dummy text of the printing Lorem Ipsum has been the industry's standard dummy text ever since the 1500s.</p><a class="more" href="#">Read More &gt;</a></article>
<article class="abs resource-card" style="left:435px"><h3 class="heading">SECTION 1.10.33 OF "DE FINIBUS BONORUM ET MALORUM</h3><p>Lorem Ipsum is simply dummy text of the printing Lorem Ipsum has been the industry's standard dummy text ever since the 1500s.</p><a class="more" href="#">Read More &gt;</a></article>
<article class="abs resource-card" style="left:780px"><h3 class="heading">SECTION 1.10.33 OF "DE FINIBUS BONORUM ET MALORUM</h3><p>Lorem Ipsum is simply dummy text of the printing Lorem Ipsum has been the industry's standard dummy text ever since the 1500s.</p><a class="more" href="#">Read More &gt;</a></article>

<h2 class="abs heading section-title" style="top:1652px">OUR TEAM</h2>
<article class="abs team-card" style="left:88px"><div class="team-photo" role="img" aria-label="Portrait of Ivan Pelkins" style="background:linear-gradient(#9a9a9a,#d4d4d4)"></div><h3 class="heading">IVAN PELKINS</h3><div class="role">Producing Branch Manager</div><p>I have over 15 years of experience in Mortgage Planning. I rank in the top 1% of loan originators in the country</p></article>
<article class="abs team-card" style="left:347px"><div class="team-photo" role="img" aria-label="Portrait of Marco Ellery" style="background:linear-gradient(#c8c8c8,#7a7a7a)"></div><h3 class="heading">MARCO ELLERY</h3><div class="role">Loan Partner</div><p>I am able to help customers with pre-qualifications and pre-approvals and keep the applicants and real estate</p></article>
<article class="abs team-card" style="left:607px"><div class="team-photo" role="img" aria-label="Portrait of Tomas Quillen" style="background:linear-gradient(#dedede,#9a9a9a)"></div><h3 class="heading">TOMAS QUILLEN</h3><div class="role">Loan Processor</div><p>I verify loan documents including income, credit, appraisal and title insurance, preparing the loan application for</p></article>
<article class="abs team-card" style="left:866px"><div class="team-photo" role="img" aria-label="Portrait of Linda Harrowgate" style="background:linear-gradient(#1a1a1a,#3a3a3a)"></div><h3 class="heading">LINDA HARROWGATE</h3><div class="role">Closing Coordinator/Team Leader</div><p>I guide our clients with any conditions or stipulations set by underwriting post loan conditional approval. I make sure</p></article>

<h2 class="abs heading section-title" style="top:2200px">LATEST BLOG</h2>
<article class="abs blog-post" style="left:88px"><h3 class="heading">LOREM IPSUM IS SIMPLY DUMMY</h3><div class="blog-image" role="img" aria-label="Photo of a house key being handed over a signed contract" style="background:linear-gradient(135deg,#3a3a3a,#b9b2a6)"></div><p>Sed ut perspiciatis unde omnis iste natus error sit voluptatem accusantium doloremque laudantium, totam rem aperiam, eaque ipsa quae ab illo inventore veritatis et quasi architecto</p><a class="more" href="#">Read More &gt;</a></article>
<article class="abs blog-post" style="left:438px"><h3 class="heading">LOREM IPSUM IS SIMPLY DUMMY</h3><div class="blog-image" role="img" aria-label="Photo of a team meeting around a laptop" style="background:linear-gradient(135deg,#d9c8a6,#8a7660)"></div><p>Sed ut perspiciatis unde omnis iste natus error sit voluptatem accusantium doloremque laudantium, totam rem aperiam, eaque ipsa quae ab illo inventore veritatis et quasi architecto</p><a class="more" href="#">Read More &gt;</a></article>
<article class="abs blog-post" style="left:786px"><h3 class="heading">LOREM IPSUM IS SIMPLY DUMMY</h3><div class="blog-image" role="img" aria-label="Photo of a loan officer meeting a couple at an office desk" style="background:linear-gradient(135deg,#7b6650,#c9b79a)"></div><p>Sed ut perspiciatis unde omnis iste natus error sit voluptatem accusantium doloremque laudantium, totam rem aperiam, eaque ipsa quae ab illo inventore veritatis et quasi architecto</p><a class="more" href="#">Read More &gt;</a></article>

<section class="abs newsletter"></section>
<h2 class="abs heading newsletter-title">READ OUR NEWSLETTER</h2>
<div class="abs newsletter-input">Email Address</div>
<a class="abs btn newsletter-btn" href="#">SUBMIT</a>

<footer class="abs site-footer"></footer>
<div class="abs footer-brand"><div class="brand-mark"></div><div class="brand-name">The Pelkins Team<br>Home Loan Group</div></div>
<div class="abs footer-divider" style="left:387px;top:2930px;height:190px"></div>
<div class="abs footer-divider" style="left:917px;top:2930px;height:190px"></div>
<h3 class="abs footer-heading" style="left:470px;top:2924px">Contact Us:</h3>
<ul class="abs contact-list">
  <li><svg width="12" height="14" viewBox="0 0 12 16"><path d="M6 0a6 6 0 0 0-6 6c0 4.5 6 10 6 10s6-5.5 6-10a6 6 0 0 0-6-6zm0 8.5a2.5 2.5 0 1 1 0-5 2.5 2.5 0 0 1 0 5z" fill="#cfcfcf"/></svg><span>Pelkins Team<br>4410 Linden Park Rd, Suite 112, Brookvale FL 32990</span></li>
  <li><svg width="14" height="14" viewBox="0 0 16 16"><path d="M3.5 1l3 3-2 2c1 2 3 4 5 5l2-2 3 3-2 2.5C7 14 2 9 1 3.5z" fill="#cfcfcf"/></svg><span>1-555-014-2287</span></li>
  <li><svg width="14" height="12" viewBox="0 0 16 12"><rect width="16" height="12" rx="1" fill="#cfcfcf"/><path d="M0 1l8 6 8-6" fill="none" stroke="#333" stroke-width="1.5"/></svg><span>info@pelkinsteam.com</span></li>
</ul>
<h3 class="abs footer-heading" style="left:1007px;top:2924px">Quick Links:</h3>
<ul class="abs links"><li>&gt; Home</li><li>&gt; About us</li><li>&gt; Mortgage 101</li><li>&gt; Contact us</li></ul>
<p class="abs legal">Licensed by the Bureau of Lending Affairs under the Pacific Credit Providers Act. Loans made or arranged pursuant to a Pacific Credit Providers Act License. Equal Housing Lender Brightwell Cannot Accept mortgage applications for properties located in New York via this site</p>
<p class="abs copyright">Copyright © 2018. Pelkins Team. All rights reserved.</p>
<div class="abs social"><span></span><span></span><span></span><span></span></div>

</body>
</html>
```